RTavenor Business Cards & Letterhead

I have a logo but need a design for some new business cards. We are a Design-Build Firm that specializes in the design and construction of commercial projects.
the cards need to be professional. no cartoon stuff.
i would like to have the cards in AI format so I can update the card as needed. Logo is provided.
Our Address is: 4187 Marlowe Ct. Apex, North Carolina 27614

```html
<!DOCTYPE html>
<html lang="en">
<head>
<meta charset="utf-8">
<title>RTavenor Business Card</title>
<link rel="stylesheet" href="https://fonts.googleapis.com/css2?family=Arimo:ital,wght@0,400;0,700;1,400;1,700&display=swap">
<style>
  :root {
    --bg: #e4e4e4;
    --paper: #f5f5f3;
    --ink: #1c1c1c;
    --blue: #0d4f94;
    --blue-dark: #063a73;
    --card-dark: #2a2a2a;
    --card-darker: #141414;
    --light-text: #ececec;
  }
  * { margin: 0; padding: 0; box-sizing: border-box; }
  html, body {
    width: 1200px; height: 1200px; overflow: hidden;
    background: var(--bg);
    font-family: "Arimo", Arial, sans-serif;
  }
  .canvas {
    position: relative; width: 1200px; height: 1200px;
  }
  .card {
    position: absolute; left: 250px; width: 700px; height: 400px;
    overflow: hidden;
    box-shadow: 0 10px 30px rgba(0,0,0,0.12);
  }
  .card--front { top: 150px; background: var(--paper); }
  .card--back {
    top: 650px;
    background: linear-gradient(160deg, var(--card-darker) 0%, var(--card-dark) 55%, #3a3a3a 100%);
  }
  .corner-arc { position: absolute; left: 0; top: 0; }
  .identity {
    position: absolute; right: 360px; top: 170px; text-align: right;
  }
  .identity__name {
    font-weight: 700; font-style: italic; font-size: 30px;
    color: var(--blue); letter-spacing: -0.3px;
  }
  .identity__role {
    font-style: italic; font-size: 16px; color: var(--ink);
    margin-top: 12px; padding-right: 6px;
  }
  .divider {
    position: absolute; left: 356px; top: 130px;
    width: 1.5px; height: 160px; background: var(--ink);
  }
  .contact {
    position: absolute; left: 378px; top: 134px;
    font-style: italic; font-size: 17px; color: var(--ink); line-height: 1.2;
  }
  .contact__address { margin-left: 12px; margin-bottom: 14px; }
  .contact__list { list-style: none; }
  .contact__item { display: flex; align-items: center; gap: 8px; margin-bottom: 4px; }
  .contact__icon { width: 14px; height: 14px; flex: none; }
  .tile { position: absolute; width: 86px; height: 86px; }
  .tile--blue { background: linear-gradient(145deg, var(--blue) 0%, var(--blue-dark) 100%); }
  .tile--top { right: 0; bottom: 86px; }
  .tile--bottom { right: 86px; bottom: 0; }
  .wordmark {
    position: absolute; left: 0; right: 0; top: 0; bottom: 0;
    display: flex; align-items: center; justify-content: center; gap: 16px;
  }
  .wordmark__square { width: 40px; height: 40px; background: var(--blue); }
  .wordmark__name {
    font-weight: 700; font-size: 60px; color: var(--light-text); letter-spacing: 1px;
  }
</style>
</head>
<body>
<main class="canvas">
  <section class="card card--front" aria-label="Business card front">
    <svg class="corner-arc" width="110" height="110" viewBox="0 0 110 110" aria-hidden="true">
      <path d="M80 0 A80 80 0 0 1 0 80 L0 106 A106 106 0 0 0 106 0 Z" fill="var(--blue)"/>
    </svg>
    <div class="identity">
      <div class="identity__name">Rowan Tavenor</div>
      <div class="identity__role">CEO</div>
    </div>
    <div class="divider"></div>
    <div class="contact">
      <p class="contact__address">4187 Marlowe Ct. Apex,<br>North Carolina 27614</p>
      <ul class="contact__list">
        <li class="contact__item">
          <svg class="contact__icon" viewBox="0 0 16 16" aria-hidden="true"><path d="M3 1l3 3-1.5 2a9 9 0 0 0 5 5L11.5 9.5l3 3-2 2.5C6 15 1 10 1 3z" fill="var(--blue)"/></svg>
          201.555.0148
        </li>
        <li class="contact__item">
          <svg class="contact__icon" viewBox="0 0 16 16" aria-hidden="true"><rect x="4" y="1" width="8" height="14" rx="1.5" fill="none" stroke="var(--blue)" stroke-width="2"/></svg>
          201.555.0193
        </li>
        <li class="contact__item">
          <svg class="contact__icon" viewBox="0 0 16 16" aria-hidden="true"><rect x="1" y="3" width="14" height="10" fill="var(--blue)"/><path d="M1 3l7 6 7-6" fill="none" stroke="#fff" stroke-width="1.2"/></svg>
          rowan@rtavenor.com
        </li>
        <li class="contact__item">
          <svg class="contact__icon" viewBox="0 0 16 16" aria-hidden="true"><circle cx="8" cy="8" r="7" fill="var(--blue)"/><path d="M1 8h14M8 1v14M8 1c-4 4-4 10 0 14M8 1c4 4 4 10 0 14" fill="none" stroke="#fff" stroke-width="1"/></svg>
          www.rtavenor.com
        </li>
      </ul>
    </div>
    <div class="tile tile--blue tile--top"></div>
    <div class="tile tile--blue tile--bottom"></div>
  </section>

  <section class="card card--back" aria-label="Business card back">
    <div class="wordmark">
      <span class="wordmark__square"></span>
      <span class="wordmark__name">RTavenor</span>
    </div>
  </section>
</main>
</body>
</html>
```